Commercial Real Estate

We need a business card design for a new commercial real estate business that specializes in apartment building brokerage. Not individual units but the entire complex. We find and represent the owners existing buildings and well as new buyers for those buildings. The design should convey trust, integrity, knowledge and growth. It should be easily read.

Target Market(s)

40 to 65 years old

Industry/Entity Type

Real Estate

```html
<!DOCTYPE html>
<html lang="en">
<head>
<meta charset="utf-8">
<title>Crestline Realty – Business Card</title>
<link rel="stylesheet" href="https://fonts.googleapis.com/css2?family=Open+Sans:wght@400;600;700&display=swap">
<style>
  :root {
    --backdrop: #ece8e2;
    --card: #ffffff;
    --ink-dark: #3a4446;
    --ink-muted: #555f61;
    --teal: #4fb3b0;
    --teal-deep: #3a9794;
    --slate: #3e4a4c;
    --shadow: rgba(40, 30, 20, 0.18);
  }
  * { box-sizing: border-box; margin: 0; padding: 0; }
  html, body {
    width: 1200px; height: 913px; overflow: hidden;
    background: var(--backdrop);
    font-family: "Open Sans", sans-serif;
  }
  .sheet {
    position: relative; width: 1200px; height: 913px;
    display: flex; align-items: center; justify-content: center; gap: 60px;
  }
  .card {
    position: relative; width: 520px; height: 298px;
    background: var(--card);
    box-shadow: 0 10px 28px var(--shadow);
    overflow: hidden;
  }
  .brand {
    display: flex; align-items: center; gap: 12px;
    color: var(--ink-dark); font-weight: 700; letter-spacing: 0.06em;
    text-transform: uppercase;
  }
  .brand-square { width: 16px; height: 16px; background: var(--teal); }
  .card--front { display: flex; align-items: center; justify-content: center; }
  .card--front .brand { font-size: 34px; }
  .card--front .brand-square { width: 22px; height: 22px; }

  .card--back .brand {
    position: absolute; top: 58px; right: 46px; font-size: 22px;
  }
  .edge-band {
    position: absolute; top: 0; right: 0; width: 14px; height: 100%;
    background: var(--teal);
  }
  .foot-band {
    position: absolute; left: 0; bottom: 0; height: 10px; width: 100%;
    background: linear-gradient(90deg, var(--slate) 0 58%, var(--teal-deep) 58% 100%);
  }
  .holder { position: absolute; left: 40px; top: 108px; }
  .holder-name { font-size: 22px; font-weight: 700; color: var(--ink-dark); line-height: 1.1; }
  .holder-role { font-size: 12px; color: var(--ink-muted); margin-top: 2px; }
  .contact {
    position: absolute; left: 130px; top: 176px; list-style: none;
    font-size: 13px; color: var(--ink-dark); line-height: 1.35;
  }
  .contact li { display: flex; align-items: flex-start; gap: 10px; margin-bottom: 3px; }
  .contact svg { width: 12px; height: 12px; margin-top: 3px; flex: none; fill: var(--teal-deep); }
  .contact .web { color: var(--teal-deep); }
</style>
</head>
<body>
<main class="sheet">
  <section class="card card--front">
    <div class="brand"><span class="brand-square"></span>Crestline Realty</div>
  </section>

  <section class="card card--back">
    <div class="brand"><span class="brand-square"></span>Crestline Realty</div>
    <div class="holder">
      <p class="holder-name">Your Name</p>
      <p class="holder-role">Director</p>
    </div>
    <ul class="contact">
      <li>
        <svg viewBox="0 0 12 12"><path d="M6 0a4 4 0 0 0-4 4c0 3 4 8 4 8s4-5 4-8a4 4 0 0 0-4-4zm0 5.5A1.5 1.5 0 1 1 6 2.5a1.5 1.5 0 0 1 0 3z"/></svg>
        <span>Your commercial address<br>in just two line</span>
      </li>
      <li>
        <svg viewBox="0 0 12 12"><path d="M2.5 0.5 4.5 3 3.4 4.4a7 7 0 0 0 4.2 4.2L9 7.5l2.5 2-1.2 1.8C5.5 11.5 0.5 6.5 0.7 1.7z"/></svg>
        <span>00000000000</span>
      </li>
      <li>
        <svg viewBox="0 0 12 12"><path d="M0 2h12v8H0zM0.8 2.6 6 6.6l5.2-4z" fill-rule="evenodd"/></svg>
        <span>yourname@website.com</span>
      </li>
      <li>
        <svg viewBox="0 0 12 12"><circle cx="6" cy="6" r="5.5"/><path d="M0.5 6h11M6 0.5c-2.4 3-2.4 8 0 11M6 0.5c2.4 3 2.4 8 0 11" stroke="#fff" stroke-width="0.9" fill="none"/></svg>
        <span class="web">www.website.com</span>
      </li>
    </ul>
    <div class="edge-band"></div>
    <div class="foot-band"></div>
  </section>
</main>
</body>
</html>
```